Dalvick's Business Card

I need some designs for a new business card including the new logo attached. An old example of our business card is also attached to show all the data that should be included on the new design.
**I added some more examples someone had mocked up**

Contact Information for Business Card

Should include all info on other examples uploaded.

```html
<!DOCTYPE html>
<html lang="en">
<head>
<meta charset="utf-8">
<title>Dalvick's Business Card</title>
<link rel="stylesheet" href="https://fonts.googleapis.com/css2?family=Montserrat:wght@500;600;700;800&display=swap">
<style>
  :root {
    --brand-blue: #0b6fb6;
    --brand-red: #e8222d;
    --paper: #ffffff;
    --backdrop: #e7e7e9;
  }
  * { box-sizing: border-box; margin: 0; padding: 0; }
  html, body {
    width: 1200px; height: 1200px; overflow: hidden;
    background: var(--backdrop);
    font-family: "Montserrat", Arial, sans-serif;
  }
  .sheet {
    width: 1200px; height: 1200px;
    display: flex; flex-direction: column; align-items: center; justify-content: center;
    gap: 56px;
  }
  .card {
    position: relative; width: 900px; height: 514px;
    background: var(--paper); overflow: hidden;
    box-shadow: 0 14px 30px rgba(0,0,0,0.18);
  }
  .card-shapes { position: absolute; inset: 0; width: 100%; height: 100%; }

  /* Front */
  .band-text {
    position: absolute; left: 0; width: 100%;
    text-align: center; color: var(--paper);
    font-weight: 600; letter-spacing: 0.5px; text-transform: uppercase;
  }
  .band-top { top: 26px; font-size: 30px; }
  .band-bottom { bottom: 24px; font-size: 22px; }

  .brand {
    position: absolute; display: flex; align-items: center; gap: 18px;
  }
  .brand-dot { border-radius: 50%; background: var(--brand-blue); flex: none; }
  .brand-words { display: flex; flex-direction: column; }
  .brand-name { color: var(--brand-blue); font-weight: 800; line-height: 1; letter-spacing: 1px; }
  .brand-tagline { color: var(--brand-red); font-weight: 700; text-transform: uppercase; text-align: right; }

  .front .brand { left: 150px; top: 190px; }
  .front .brand-dot { width: 92px; height: 92px; }
  .front .brand-name { font-size: 96px; }
  .front .brand-tagline { font-size: 19px; margin-top: 6px; }

  /* Back */
  .back .brand { left: 56px; top: 54px; gap: 14px; }
  .back .brand-dot { width: 58px; height: 58px; }
  .back .brand-name { font-size: 54px; }
  .back .brand-tagline { font-size: 12px; margin-top: 4px; }

  .owner { position: absolute; left: 56px; top: 350px; }
  .owner-name { color: var(--brand-red); font-weight: 800; font-size: 44px; text-transform: uppercase; }
  .owner-role { color: var(--paper); font-weight: 500; font-size: 24px; text-transform: uppercase; margin-top: 14px; letter-spacing: 0.5px; }

  .divider { position: absolute; left: 478px; top: 390px; width: 5px; height: 28px; background: var(--paper); }

  .contact { position: absolute; left: 512px; top: 300px; color: var(--paper); list-style: none; }
  .contact li { display: flex; align-items: center; gap: 12px; font-size: 25px; font-weight: 500; line-height: 1.5; }
  .contact .icon { width: 20px; height: 20px; flex: none; }
  .contact .motto { text-transform: uppercase; font-size: 24px; margin-top: 12px; padding-left: 32px; letter-spacing: 0.5px; }
</style>
</head>
<body>
<main class="sheet">

  <section class="card front" aria-label="Card front">
    <svg class="card-shapes" viewBox="0 0 900 514" aria-hidden="true">
      <path d="M0,0 H900 V92 H400 L380,114 L360,92 H0 Z" fill="var(--brand-blue)"/>
      <path d="M0,430 H420 L440,408 L460,430 H900 V514 H0 Z" fill="var(--brand-red)"/>
    </svg>
    <p class="band-text band-top">Serves Cedar Hollow, IA &amp; Surrounding Areas</p>
    <div class="brand">
      <span class="brand-dot"></span>
      <div class="brand-words">
        <span class="brand-name">DALVICK'S</span>
        <span class="brand-tagline">Air Conditioning &amp; Heating Service</span>
      </div>
    </div>
    <p class="band-text band-bottom">Call today for all your HVAC, refrigeration &amp; plumbing needs</p>
  </section>

  <section class="card back" aria-label="Card back">
    <svg class="card-shapes" viewBox="0 0 900 514" aria-hidden="true">
      <path d="M0,270 C260,268 420,190 560,110 C690,36 800,0 900,0 V514 H0 Z" fill="var(--brand-red)"/>
      <path d="M0,296 C270,294 440,214 580,134 C700,64 810,34 900,30 V514 H0 Z" fill="var(--brand-blue)" stroke="var(--paper)" stroke-width="4"/>
    </svg>
    <div class="brand">
      <span class="brand-dot"></span>
      <div class="brand-words">
        <span class="brand-name">DALVICK'S</span>
        <span class="brand-tagline">Air Conditioning &amp; Heating Service</span>
      </div>
    </div>
    <div class="owner">
      <p class="owner-name">Dean Dalvick</p>
      <p class="owner-role">Licensed &amp; Insured</p>
    </div>
    <span class="divider"></span>
    <ul class="contact">
      <li>
        <svg class="icon" viewBox="0 0 24 24" aria-hidden="true"><path d="M6.6 10.8a15 15 0 0 0 6.6 6.6l2.2-2.2a1 1 0 0 1 1-.25 11.4 11.4 0 0 0 3.6.57 1 1 0 0 1 1 1V20a1 1 0 0 1-1 1A17 17 0 0 1 3 4a1 1 0 0 1 1-1h3.5a1 1 0 0 1 1 1c0 1.25.2 2.45.57 3.57a1 1 0 0 1-.25 1z" fill="var(--brand-red)"/></svg>
        555.014.2290
      </li>
      <li>
        <svg class="icon" viewBox="0 0 24 24" aria-hidden="true"><rect x="2" y="5" width="20" height="14" rx="1.5" fill="var(--brand-red)"/><path d="M3 6l9 7 9-7" fill="none" stroke="var(--paper)" stroke-width="1.8"/></svg>
        hvacdalvick@mailbox.com
      </li>
      <li class="motto">Family Owned &amp; Operated</li>
    </ul>
  </section>

</main>
</body>
</html>
```